Professional Package for CPA Firm

We would like a stationery design for our new CPA Firm based in Atlanta, GA called 'Vale 8'. We work with investors to help grow investments, tax free. We would like the design to have a professional/minimal look with a 'wow' factor. We need 9.5″ x 4.125″, 9x12, and 10x13 mailing envelopes, business cards, and a letterhead. We have a logo that is already complete. For the letterhead, we would like to have space to put credentials at the bottom of the page

Industry/Entity Type

CPA, Accounting

```html
<!DOCTYPE html>
<html lang="en">
<head>
<meta charset="utf-8">
<title>Vale 8 — Business Card</title>
<link href="https://fonts.googleapis.com/css2?family=Lato:wght@400;700;900&display=swap" rel="stylesheet">
<style>
  :root {
    --backdrop: #9a9a9a;
    --card-white: #ffffff;
    --navy: #06283d;
    --navy-deep: #022b3e;
    --teal: #1aa6b7;
    --sky: #1b8fc7;
    --text-grey: #444a4f;
  }
  * { margin: 0; padding: 0; box-sizing: border-box; }
  html, body {
    width: 1200px; height: 1200px; overflow: hidden;
    background: var(--backdrop);
    font-family: "Lato", Arial, sans-serif;
  }
  .canvas { position: relative; width: 1200px; height: 1200px; }

  .card { position: absolute; left: 262px; width: 686px; height: 392px; }
  .card-front { top: 165px; background: var(--card-white); }
  .card-back { top: 653px; background: var(--navy-deep); }

  .brand-name {
    position: absolute; left: 46px; top: 38px;
    font-weight: 900; font-size: 72px; line-height: 1;
    letter-spacing: 4px; color: var(--navy);
  }
  .brand-tagline {
    position: absolute; left: 47px; top: 122px;
    font-size: 18px; letter-spacing: 2.6px; color: var(--navy);
  }

  .person-name {
    position: absolute; left: 46px; top: 176px;
    font-weight: 700; font-size: 23px; color: var(--navy); letter-spacing: 0.3px;
  }
  .person-title {
    position: absolute; left: 46px; top: 204px;
    font-size: 16px; color: var(--teal);
  }
  .address {
    position: absolute; left: 47px; top: 232px;
    font-size: 16px; line-height: 19px; color: var(--text-grey);
  }
  .contact-list {
    position: absolute; left: 47px; top: 279px; list-style: none;
  }
  .contact-list li {
    display: flex; align-items: center; gap: 10px;
    font-size: 16px; line-height: 19.5px; color: var(--text-grey);
  }
  .contact-list svg { width: 11px; height: 11px; fill: var(--teal); flex: none; }

  .back-brand {
    position: absolute; left: 0; right: 0; top: 210px; text-align: center;
    color: var(--sky);
  }
  .back-brand .brand-mark {
    font-weight: 900; font-size: 62px; line-height: 1; letter-spacing: 4px;
  }
  .back-brand .brand-line {
    margin-top: 10px; font-size: 16px; letter-spacing: 2.6px;
  }
</style>
</head>
<body>
<div class="canvas">

  <section class="card card-front">
    <div class="brand-name">VALE 8</div>
    <div class="brand-tagline">CPAs and Tax Advisors</div>

    <div class="person-name">DANIEL HARPER</div>
    <div class="person-title">President</div>

    <address class="address" style="font-style:normal">
      4210 Birchwood Lane<br>
      Marietta, Georgia 30062
    </address>

    <ul class="contact-list">
      <li>
        <svg viewBox="0 0 12 12" aria-hidden="true"><path d="M2.5 0.5 L4.3 0.5 L5 3.2 L3.8 4.2 C4.5 5.8 6 7.4 7.8 8.2 L8.8 7 L11.5 7.7 L11.5 9.5 C11.5 10.6 10.6 11.5 9.5 11.5 C4.5 11.2 0.8 7.5 0.5 2.5 C0.5 1.4 1.4 0.5 2.5 0.5 Z"/></svg>
        404-555-0182
      </li>
      <li>
        <svg viewBox="0 0 12 12" aria-hidden="true"><path d="M3 0 H9 A1 1 0 0 1 10 1 V11 A1 1 0 0 1 9 12 H3 A1 1 0 0 1 2 11 V1 A1 1 0 0 1 3 0 Z M3.3 1.5 V9.5 H8.7 V1.5 Z M5.4 10.2 H6.6 V11.2 H5.4 Z"/></svg>
        404-555-0147
      </li>
      <li>
        <svg viewBox="0 0 12 12" aria-hidden="true"><path d="M0.5 2.5 H11.5 V10 H0.5 Z M1.5 3.4 L6 6.6 L10.5 3.4 V3.3 H1.5 Z"/></svg>
        info@vale8.com
      </li>
      <li>
        <svg viewBox="0 0 12 12" aria-hidden="true"><circle cx="6" cy="6" r="5.5"/><path d="M3 3.5 C4 3 5 4 4.5 5 C4 6 5.5 6.5 5 8 L4 9.5 C2.5 8.5 2 6 3 3.5 Z M7 2 C8.5 2.5 9.5 4 9 5 C8 5.5 7 4.5 7 2 Z" fill="#ffffff"/></svg>
        www.vale8.com
      </li>
    </ul>
  </section>

  <section class="card card-back">
    <div class="back-brand">
      <div class="brand-mark">VALE 8</div>
      <div class="brand-line">CPAs and Tax Advisors</div>
    </div>
  </section>

</div>
</body>
</html>
```